Personalized Technology Company Needs a Business Card

I need a double-sided business card. Both sides will have the logo, and the contact information. One side will be black, with the white / gray logo, and the other will be white, with the black / gray logo. The black side will have the text "Custom Gaming PC's" and will have a water-cooled gaming PC image. The white side will have the text "Custom Business Computers & Consulting", and will have a business / enterprise PC image. Feel free to add a conservative image in the background, while the color remains unchanged. I'm uploading the base logo (transparent), so you can modify the colors, both the finished colored logos and an idea of ​​the business card (with the current information, just missing the website, which is www.velomindsystems.com, please add it.) Thank you so much for your effort, I'll be specting your cool designs. Good Luck!

Target Market(s)

Gamers & Entrepreneurs / Business Owners / Chief Technology Officers

Industry/Entity Type

Technology Equipment

Contact Information for Business Card

I need a double-sided business card. Both sides will have the logo, and the contact information. One side will be black, with the white/gray logo, and the other one will be white, with the black/gray logo. The black side will have the text "Custom Gaming PC's" and will have a water-cooled gaming PC image. The white side will have the text "Custom Business Computers & Consulting", and will have a business/enterprise PC image. Feel free to add a conservative image in the background, whilst the color remains unchanged.

I'm uploading the base logo (transparent), so you can modify the colors, both the finished colored logos and an idea of the business card (with the actual information, just missing the website, which is www.velomindsystems.com, please add it.)

Thank you so much for your effort, I'll be specting your cool designs. Good Luck!

Font styles to use
Serif

Colors
000000
757575
ffffff

Requirements
Must have
• Please See Description
Nice to have
• Please See Description
Should not have
• Please See Description

```html
<!DOCTYPE html>
<html lang="en">
<head>
<meta charset="UTF-8">
<title>Velomind Systems – Business Card</title>
<link rel="stylesheet" href="https://fonts.googleapis.com/css2?family=Michroma&family=Questrial&display=swap">
<style>
  :root {
    --backdrop: #b4b4ae;
    --card-dark: #05070d;
    --card-light: #f7f7f7;
    --ink-white: #ffffff;
    --ink-black: #111111;
    --ink-gray: #757575;
    --accent-blue: #1d45d8;
    --rule: #555555;
  }
  * { margin: 0; padding: 0; box-sizing: border-box; }
  html, body { width: 1200px; height: 900px; overflow: hidden; }
  body { background: var(--backdrop); position: relative; font-family: "Questrial", sans-serif; }

  .card {
    position: absolute;
    top: 291px;
    width: 530px;
    height: 319px;
    border-radius: 20px;
    overflow: hidden;
  }
  .card--gaming { left: 53px; background: var(--card-dark); }
  .card--business { left: 626px; background: var(--card-light); }

  .photo-gaming-pc {
    position: absolute; inset: 0;
    background:
      radial-gradient(ellipse at 60% 30%, rgba(40, 80, 170, 0.75), transparent 60%),
      linear-gradient(120deg, #0a1630 0%, #123068 45%, #0b1a3a 70%, #02040a 100%);
  }
  .photo-business-laptop {
    position: absolute; left: 265px; top: 28px; width: 250px; height: 190px;
    border-radius: 6px;
    background: linear-gradient(160deg, #ececec 0%, #e2e2e2 60%, #efefef 100%);
  }

  .brand { position: absolute; display: flex; align-items: center; gap: 16px; }
  .brand__dot { width: 58px; height: 58px; border-radius: 50%; flex: none; }
  .brand__name {
    font-family: "Michroma", sans-serif;
    font-size: 30px; line-height: 1.15; letter-spacing: 3px;
    text-transform: uppercase;
  }
  .card--gaming .brand { left: 112px; top: 127px; }
  .card--gaming .brand__dot { background: var(--ink-gray); }
  .card--gaming .brand__name { color: var(--ink-white); }
  .card--business .brand { left: 150px; top: 102px; }
  .card--business .brand__dot { background: var(--ink-black); }
  .card--business .brand__name { color: var(--ink-black); }

  .tagline-gaming {
    position: absolute; left: 0; right: 0; top: 248px;
    text-align: center;
    font-family: "Michroma", sans-serif;
    font-size: 26px; letter-spacing: 4px; text-transform: uppercase;
    color: var(--ink-white);
  }
  .highlight { color: var(--accent-blue); }

  .tagline-business {
    position: absolute; right: 33px; top: 206px;
    text-align: right; text-transform: uppercase;
    font-size: 21px; line-height: 27px; color: #222;
  }

  .web-line {
    position: absolute; left: 0; top: 286px; width: 272px;
    border-top: 1px solid var(--rule);
  }
  .web-address {
    position: absolute; right: 16px; top: 276px;
    display: flex; align-items: center; gap: 4px;
    font-size: 14px; color: #222;
  }
</style>
</head>
<body>
  <section class="card card--gaming">
    <div class="photo-gaming-pc" role="img" aria-label="Water-cooled gaming PC interior with blue lighting"></div>
    <div class="brand">
      <span class="brand__dot"></span>
      <span class="brand__name">Velomind<br>Systems</span>
    </div>
    <p class="tagline-gaming">Custom <span class="highlight">Gaming</span> PC</p>
  </section>

  <section class="card card--business">
    <div class="photo-business-laptop" role="img" aria-label="Faint business laptop computer"></div>
    <div class="brand">
      <span class="brand__dot"></span>
      <span class="brand__name">Velomind<br>Systems</span>
    </div>
    <p class="tagline-business">Custom <span class="highlight">Business</span><br>Computers &amp; Consulting</p>
    <div class="web-line"></div>
    <p class="web-address">www.velomindsystems.com
      <svg width="11" height="11" viewBox="0 0 12 12" aria-hidden="true">
        <circle cx="6" cy="6" r="5" fill="none" stroke="#444" stroke-width="1"/>
        <ellipse cx="6" cy="6" rx="2.2" ry="5" fill="none" stroke="#444" stroke-width="0.8"/>
        <line x1="1" y1="6" x2="11" y2="6" stroke="#444" stroke-width="0.8"/>
      </svg>
    </p>
  </section>
</body>
</html>
```